Plakate für ein Fest
Zielgruppe
Das Kessner Park ist ein Gewerbepark mit unterschiedlichen Mietern von Handwerker über Musiker bis hin zu Vermögensberatung. Wir veranstalten ein Fest für unsere Mieter und möchten dieses Plakat als Einladung nutzen.
Aufgabenstellung
Hintergrund schwarz, Logo verwenden
Get together
BBQ & Cocktails im Kessner Park
am 13.10.2023 ab 18 Uhr
Logo Band wild pebbles
Kinderbereich
Wir freuen uns darauf, alle Mieter mit Familien begrüßen zu dürfen! Auch an die Kleinen haben wir gedacht.

```html
<!DOCTYPE html>
<html lang="de">
<head>
<meta charset="utf-8">
<title>Get together – Kessner Park</title>
<link rel="stylesheet" href="https://fonts.googleapis.com/css2?family=PT+Serif:wght@400;700&family=Tinos&display=swap">
<style>
  :root {
    --bg: #000000;
    --cream: #f6ecdc;
    --gold: #c59a22;
    --rule: #e9e2d6;
    --logo-box: #161616;
    --logo-accent: #2fae53;
    --photo-sky: #f4f6ee;
    --photo-tree: #6f8c6a;
    --photo-grass: #b9c43c;
    --photo-warm: #e59a4a;
  }
  * { margin: 0; padding: 0; box-sizing: border-box; }
  html, body { width: 848px; height: 1200px; overflow: hidden; background: var(--bg); }
  .poster {
    position: relative;
    width: 848px;
    height: 1200px;
    background: var(--bg);
    font-family: "PT Serif", Georgia, serif;
    color: var(--cream);
  }
  .rule {
    position: absolute;
    left: 52px;
    width: 746px;
    height: 1px;
    background: var(--rule);
  }
  .title {
    position: absolute;
    top: 30px;
    left: 0;
    width: 848px;
    text-align: center;
    font-weight: 700;
    font-size: 96px;
    line-height: 110px;
    letter-spacing: -0.5px;
    color: var(--cream);
  }
  .subtitle {
    position: absolute;
    top: 164px;
    left: 0;
    width: 848px;
    text-align: center;
    font-weight: 700;
    font-size: 21px;
    line-height: 28px;
    letter-spacing: 5.4px;
    color: var(--gold);
  }
  .photo {
    position: absolute;
    left: 52px;
    top: 230px;
    width: 746px;
    height: 579px;
    background:
      radial-gradient(ellipse at 95% 15%, rgba(229,154,74,0.75), transparent 40%),
      radial-gradient(ellipse at 40% 10%, var(--photo-sky), transparent 55%),
      linear-gradient(180deg, #cfd8cc 0%, var(--photo-tree) 38%, #8ea048 62%, var(--photo-grass) 100%);
  }
  .date {
    position: absolute;
    top: 852px;
    left: 0;
    width: 848px;
    text-align: center;
    font-weight: 700;
    font-size: 36px;
    line-height: 46px;
    letter-spacing: 5.4px;
    color: var(--gold);
  }
  .divider {
    position: absolute;
    left: 374px;
    top: 911px;
    width: 1px;
    height: 173px;
    background: var(--rule);
  }
  .band {
    position: absolute;
    left: 52px;
    top: 918px;
    width: 312px;
    font-family: "Tinos", "Times New Roman", serif;
  }
  .band-label {
    font-size: 56px;
    line-height: 60px;
    letter-spacing: 0;
    color: var(--cream);
    white-space: nowrap;
  }
  .band-name {
    font-size: 46px;
    line-height: 60px;
    letter-spacing: -1.5px;
    color: var(--gold);
    white-space: nowrap;
  }
  .band-mark {
    margin-top: 0;
    padding-left: 16px;
    font-family: "PT Serif", Georgia, serif;
    font-weight: 700;
    font-size: 32px;
    line-height: 38px;
    letter-spacing: 2px;
    color: #ffffff;
    white-space: nowrap;
  }
  .invitation {
    position: absolute;
    left: 391px;
    top: 918px;
    width: 407px;
    font-weight: 700;
    font-size: 14.5px;
    line-height: 33px;
    letter-spacing: 3px;
    color: var(--cream);
    text-transform: uppercase;
  }
  .invitation .line { display: block; white-space: nowrap; text-align: justify; text-align-last: justify; }
  .invitation .line.center { text-align: center; text-align-last: center; }
  .host-logo {
    position: absolute;
    left: 326px;
    top: 1092px;
    width: 197px;
    height: 63px;
    background: var(--logo-box);
    display: flex;
    align-items: center;
    justify-content: center;
    gap: 10px;
  }
  .host-logo .mark {
    width: 14px;
    height: 14px;
    background: var(--logo-accent);
  }
  .host-logo .name {
    font-weight: 700;
    font-size: 19px;
    line-height: 1;
    letter-spacing: 1px;
    color: #ffffff;
    text-transform: uppercase;
  }
</style>
</head>
<body>
<main class="poster">
  <div class="rule" style="top:34px"></div>
  <h1 class="title">Get together</h1>
  <div class="rule" style="top:152px"></div>
  <p class="subtitle">BBQ &amp; COCKTAILS IM KESSNER PARK</p>
  <div class="rule" style="top:204px"></div>

  <div class="photo" role="img" aria-label="Foto: Grillfest im Garten, ein Mann grillt an einem Kugelgrill, im Hintergrund Gäste am Tisch auf sonniger Wiese"></div>

  <div class="rule" style="top:840px"></div>
  <p class="date">AM 13.10.2023 AB 18 UHR</p>
  <div class="rule" style="top:911px"></div>

  <section class="band">
    <div class="band-label">LIVE-BAND</div>
    <div class="band-name">WILD PEBBLES</div>
    <div class="band-mark">wild pebbles</div>
  </section>

  <div class="divider"></div>

  <p class="invitation">
    <span class="line">Wir freuen uns darauf, alle</span>
    <span class="line">Mieter mit Familien begrüssen</span>
    <span class="line">zu dürfen! Auch an die Kleinen</span>
    <span class="line center">haben wir gedacht.</span>
    <span class="line center">Kinderbereich!</span>
  </p>

  <div class="rule" style="top:1084px"></div>

  <div class="host-logo">
    <span class="mark"></span>
    <span class="name">Kessner Park</span>
  </div>

  <div class="rule" style="top:1163px"></div>
</main>
</body>
</html>
```